Flat bootstrap design for existing site

I'm looking for a modern flat design based around an existing logo. This has to be a custom design (no external templates), and implemented into a bootstrap framework.

The logo is attached as 2 versions - choose whichever you want, that flows better with whatever design you choose.

Added screenshots of the existing site (currently using the default bootstrap layouts). Please make your designs around those pages in the screenshots (i.e. the homepage only has the postal code input and the header). The active page has 3 screenshots, because I wanted to illustrate the other states that would be visible (in the table rows).

This is a moving/junk removal website, just for some context.

Here's some example websites (flat designs) that I like, just to give you an idea of what I'm after.

https://www.plimvora.com/
https://dacklow.com/
https://trevanu.com/
https://quobrintal.com/en/

Coding

Coded - Design and coding required

Number of Pages Required

5+ page

Colors

Designer to choose colors to be used in the design.

Requirements
Must have
• It must be a modern/simple flat design, that is built around the existing logo (attached).
• It has to be implemented using bootstrap.

```html
<!DOCTYPE html>
<html lang="en">
<head>
<meta charset="utf-8">
<title>Haulwick – Sign in</title>
<link rel="stylesheet" href="https://fonts.googleapis.com/css2?family=Montserrat:wght@400;500&family=Open+Sans:wght@300;400;700&display=swap">
<style>
  :root {
    --brand: #4bc8f5;
    --page-bg: #e9e9eb;
    --surface: #ffffff;
    --ink: #1d1d1f;
    --muted: #555a60;
    --field-border: #6b6f75;
  }
  * { box-sizing: border-box; margin: 0; padding: 0; }
  html, body {
    width: 1200px; height: 720px; overflow: hidden;
    background: var(--page-bg);
    font-family: "Montserrat", sans-serif;
    color: var(--ink);
  }
  .site-header {
    position: absolute; left: 0; top: 0; width: 1200px; height: 85px;
    background: var(--surface);
    box-shadow: 0 4px 14px rgba(0,0,0,0.05);
  }
  .brand {
    position: absolute; left: 131px; top: 22px;
    display: flex; align-items: center; gap: 8px;
    font-family: "Open Sans", sans-serif; font-weight: 700;
    font-size: 30px; color: var(--brand); letter-spacing: 0.5px;
    text-decoration: none;
  }
  .brand-dot { width: 14px; height: 14px; border-radius: 50%; background: var(--brand); }
  .main-nav {
    position: absolute; top: 26px; left: 718px;
    display: flex; align-items: center; height: 29px;
  }
  .main-nav a {
    font-size: 11px; color: var(--ink); text-decoration: none;
    letter-spacing: 0.2px; white-space: nowrap;
  }
  .nav-book { margin-right: 30px; }
  .nav-how { margin-right: 28px; }
  .nav-driver {
    display: flex; align-items: center; justify-content: center;
    width: 126px; height: 29px; border: 1px solid var(--brand);
    color: var(--brand) !important; margin-right: 19px;
  }
  .page-title {
    position: absolute; left: 322px; top: 164px;
    font-family: "Open Sans", sans-serif; font-weight: 300;
    font-size: 34px; color: var(--ink);
  }
  .signin-card {
    position: absolute; left: 326px; top: 244px;
    width: 548px; height: 360px; background: var(--surface);
  }
  .field {
    position: absolute; left: 48px; width: 456px; height: 64px;
    border: 1px solid var(--field-border);
    display: flex; align-items: center; padding-left: 25px;
    font-size: 12px; color: var(--ink);
  }
  .field-email { top: 42px; left: 48px; }
  .field-password { top: 133px; left: 50px; }
  .field svg { width: 12px; height: 12px; margin-right: 15px; fill: var(--muted); }
  .login-button {
    position: absolute; left: 198px; top: 238px;
    width: 153px; height: 56px; border: none;
    background: var(--brand); color: var(--surface);
    font-family: "Open Sans", sans-serif; font-weight: 700;
    font-size: 18px; letter-spacing: 1px;
  }
</style>
</head>
<body>
  <header class="site-header">
    <a class="brand" href="#"><span class="brand-dot"></span>Haulwick</a>
    <nav class="main-nav">
      <a class="nav-book" href="#">BOOK</a>
      <a class="nav-how" href="#">HOW IT WORKS</a>
      <a class="nav-driver" href="#">BECOME A DRIVER</a>
      <a class="nav-signin" href="#">SIGN IN</a>
    </nav>
  </header>

  <h1 class="page-title">Please Sign in</h1>

  <form class="signin-card">
    <label class="field field-email">
      <svg viewBox="0 0 12 12" aria-hidden="true"><path d="M0 2h12v1.2L6 6.6 0 3.2z"/><path d="M0 4.4l6 3.4 6-3.4V10H0z"/></svg>
      E mail Address
    </label>
    <label class="field field-password">
      <svg viewBox="0 0 12 12" aria-hidden="true"><path d="M3 5V3.6a3 3 0 0 1 6 0V5H7.6V3.6a1.6 1.6 0 0 0-3.2 0V5z"/><rect x="1.8" y="5" width="8.4" height="6.5" rx="0.6"/></svg>
      Password
    </label>
    <button class="login-button" type="button">LOGIN</button>
  </form>
</body>
</html>
```